Modern design company business card design

We are a design oriented construction firm. The owner is an architect and licensed General Contractor and accomplished furniture designer. We do new home construction and large scale remodeling and office design. We would like a design for our new business cards that is clean and modern, but relatable. We like the bright green color of our logo mixed with different shades of grey. We're also open to reinterpreting the logo.

Target Market(s)

Potential design clients,
Construction clients

Industry/Entity Type

Architecture

Contact Information for Business Card

Tall Maple Design | Build Inc. (optional with logo, Inc. optional)Jeffrey MorganOwner (optional)317.555.0148 cell317.431.8056 officejmorgan@greensquareinc.comwww.greensquareinc.com

Font styles to use
Sans Serif
Other font styles liked:
• Avenir

Requirements
Nice to have
• I like designs that have some continuity between the front and back, i.e. similar layouts or graphic elements that wrap around the card. I tend to prefer horizontal over vertical, but that's not a have to. I also tend to prefer white or recycled paper.

```html
<!DOCTYPE html>
<html lang="en">
<head>
<meta charset="utf-8">
<title>Tall Maple Design | Build – Business Card</title>
<link rel="stylesheet" href="https://fonts.googleapis.com/css2?family=Nunito+Sans:ital,wght@0,400;1,400&display=swap">
<style>
  :root {
    --green-light: #c4de6c;
    --green-mid: #a5d365;
    --green-deep: #7dc45a;
    --grey-text: #4a4a4a;
    --grey-soft: #8c8c8c;
    --paper: #ffffff;
    --backdrop: #3a3a3a;
  }
  * { margin: 0; padding: 0; box-sizing: border-box; }
  html, body {
    width: 1105px; height: 1200px; overflow: hidden;
    background: var(--backdrop);
    font-family: "Nunito Sans", sans-serif;
  }
  .card {
    position: absolute; left: 192px; width: 720px; height: 412px; overflow: hidden;
  }
  .card--front { top: 146px; background: var(--paper); }
  .card--back {
    top: 602px;
    background: linear-gradient(to bottom, var(--green-light), var(--green-mid) 55%, var(--green-deep));
  }

  /* Front: company name */
  .brand { position: absolute; left: 41px; top: 112px; }
  .brand__name {
    display: block; font-size: 31px; font-weight: 400; letter-spacing: 2px;
    color: var(--grey-soft); text-transform: uppercase; line-height: 1;
  }
  .brand__tagline {
    display: block; margin-top: 8px; font-size: 14px; font-weight: 400; letter-spacing: 1.5px;
    color: var(--grey-soft); text-transform: uppercase;
  }

  /* Front: contacts */
  .contacts { position: absolute; left: 41px; top: 255px; list-style: none; }
  .contacts__item {
    display: flex; align-items: center; gap: 8px; height: 28.5px;
    font-size: 20px; color: var(--grey-text);
  }
  .contacts__item--small { font-size: 19px; }
  .contacts__icon { width: 18px; height: 18px; fill: var(--grey-text); flex: none; }

  /* Front: name band */
  .nameband {
    position: absolute; left: 468px; top: 296px; width: 252px; height: 67px;
    background: linear-gradient(to bottom, var(--green-light), var(--green-deep));
    padding: 6px 0 0 18px; color: var(--paper);
  }
  .nameband__name { font-size: 23px; font-weight: 400; text-transform: uppercase; line-height: 1.15; white-space: nowrap; }
  .nameband__role { font-size: 17px; font-weight: 400; text-transform: uppercase; }

  /* Back */
  .back-name {
    position: absolute; left: 0; right: 0; top: 186px; text-align: center;
    font-size: 31px; font-weight: 400; letter-spacing: 2px; color: var(--paper);
    text-transform: uppercase; line-height: 1;
  }
  .back-url {
    position: absolute; left: 0; right: 0; top: 342px; text-align: center;
    font-size: 18px; font-style: italic; letter-spacing: 2px; color: var(--paper);
  }
</style>
</head>
<body>
  <section class="card card--front">
    <div class="brand">
      <span class="brand__name">Tall Maple</span>
      <span class="brand__tagline">Design | Build</span>
    </div>

    <ul class="contacts">
      <li class="contacts__item">
        <svg class="contacts__icon" viewBox="0 0 24 24" aria-hidden="true"><path d="M6.6 10.8a15.1 15.1 0 0 0 6.6 6.6l2.2-2.2a1 1 0 0 1 1-.25 11.4 11.4 0 0 0 3.6.57 1 1 0 0 1 1 1V20a1 1 0 0 1-1 1A17 17 0 0 1 3 4a1 1 0 0 1 1-1h3.5a1 1 0 0 1 1 1c0 1.25.2 2.45.57 3.6a1 1 0 0 1-.25 1z"/></svg>
        <span>317.555.0148</span>
      </li>
      <li class="contacts__item">
        <svg class="contacts__icon" viewBox="0 0 24 24" aria-hidden="true"><path d="M7 1h10a2 2 0 0 1 2 2v18a2 2 0 0 1-2 2H7a2 2 0 0 1-2-2V3a2 2 0 0 1 2-2zm0 3v14h10V4zm5 15.5a1 1 0 1 0 0 2 1 1 0 0 0 0-2z"/></svg>
        <span>317.555.0172</span>
      </li>
      <li class="contacts__item contacts__item--small">
        <svg class="contacts__icon" viewBox="0 0 24 24" aria-hidden="true"><circle cx="12" cy="12" r="10"/><path d="M5 9c2 0 3 1 3 3s2 2 2 4v4M14 3c0 2 1 3 3 3s3 2 3 3" stroke="#fff" stroke-width="1.6" fill="none"/></svg>
        <span>www.tallmapleinc.example</span>
      </li>
      <li class="contacts__item contacts__item--small">
        <svg class="contacts__icon" viewBox="0 0 24 24" aria-hidden="true"><path d="M2 5h20v14H2z"/><path d="M2 5l10 8 10-8" stroke="#fff" stroke-width="1.6" fill="none"/></svg>
        <span>dholloway@tallmapleinc.example</span>
      </li>
    </ul>

    <div class="nameband">
      <div class="nameband__name">Dennis Holloway</div>
      <div class="nameband__role">Owner</div>
    </div>
  </section>

  <section class="card card--back">
    <p class="back-name">Tall Maple</p>
    <p class="back-url">www.tallmapleinc.example</p>
  </section>
</body>
</html>
```